Create website for home automation - Control your lighting, fans, blinds etc remotely by smartphone

Plan for SHOPIFY Website - Our Clever Dwelling
Company name: Our Clever Dwelling
Company Slogan: Calm Evenings Come Naturally
Clean, Modern, Easy to Navigate, easy to maintain - not a lot of coding. We need flash technology but displaying simply what we do.
What we provide:
We will be offering wireless switch which can be added to iOS/Android App via WiFi, allowing users to remotely turn on/off connected lights, fans, security cameras, appliances, irrigation, humidifier separately from anywhere at any time.
Control your home away from home. No more wandering of your mind on those lights or appliances which you might have left switched on. No need to drive back home to check and switch them off. Save that energy, money and time just with a click of your phone no matter how far you are from home.
Replace your home electrical switches with smart switches. They retrofit existing electrical switches and allow you to make the transformation as needed.
Easy to use and intuitive app allows you to control your lights and devices just at a click. Set any kind of ambiance suiting your occasion.
Set scenes in smartphone app to group and operate your devices just at a button click. Same device can be included in more than one scene.
Collections and Products
Light Switches
Wall Plugs
Fan Switch
Pendants etc special lighting types.
Light Dimmers
Blind Controllers
Home Page:
Home page needs to telling customers what we do and how we do it in a few words to grab people.
Phone
Email
Support – Download instructions per product
Client login
Wholesale login
Promotional video to be on home screen - this is a short 1.5 - 2 min illustration introduction video to who we are and what we do - this is yet to be created)
Social media link - Facebook
Pages:
FAQ
About Us
Support/Shipping/Returns policy
Support/Installation
Blog posts
Product pages:
Description
Price
Space for where a video will be featured - how each product works/installation.
Reviews
Our competition:
http://www.brivo.com.au
https://lumigardenhub.com.au/2018/04/05/best-smart-light-switches-and-plugs/
https://www.tavelinq.com

```html
<!DOCTYPE html>
<html lang="en">
<head>
<meta charset="utf-8">
<title>About Us – Our Clever Dwelling</title>
<link href="https://fonts.googleapis.com/css2?family=Mulish:wght@400;500&family=Ubuntu:wght@500;700&display=swap" rel="stylesheet">
<style>
  :root {
    --brand-navy: #10307f;
    --brand-blue: #1b73c0;
    --ink: #1c1c1c;
    --nav-ink: #444444;
    --footer-bg: #262626;
    --footer-ink: #ffffff;
    --icon-blue: #1b78c8;
    --hero-deep: #0b4f93;
    --hero-mid: #1477c6;
    --hero-light: #2e9be0;
    --page-bg: #ffffff;
  }
  * { box-sizing: border-box; margin: 0; padding: 0; }
  html, body { width: 960px; height: 1200px; overflow: hidden; background: var(--page-bg); }
  body { font-family: "Mulish", Arial, sans-serif; color: var(--ink); position: relative; }

  .site-header { position: absolute; top: 0; left: 0; width: 960px; height: 92px; }
  .brand-mark { position: absolute; left: 122px; top: 34px; display: flex; align-items: center; gap: 8px; }
  .brand-mark__dot { width: 16px; height: 16px; background: var(--brand-blue); border-radius: 50%; }
  .brand-mark__name { font-family: "Ubuntu", sans-serif; font-weight: 700; font-size: 14px; color: var(--brand-navy); }
  .main-nav { position: absolute; right: 112px; top: 37px; display: flex; gap: 26px; }
  .main-nav a { font-size: 11.5px; color: var(--nav-ink); text-decoration: none; }

  .hero { position: absolute; top: 92px; left: 0; width: 960px; height: 253px;
    background: radial-gradient(ellipse at 70% 30%, var(--hero-light) 0%, var(--hero-mid) 45%, var(--hero-deep) 100%);
    display: flex; align-items: center; justify-content: center; }
  .hero__title { font-family: "Mulish", sans-serif; font-weight: 400; font-size: 45px; color: #fff; letter-spacing: 0.5px; }

  .intro-symbol { position: absolute; left: 190px; top: 430px; width: 180px; height: 180px; border-radius: 50%; background: var(--brand-blue); opacity: 0.85; }
  .intro-block { position: absolute; left: 434px; top: 455px; width: 400px; text-align: center; }
  .intro-block__name { font-family: "Ubuntu", sans-serif; font-weight: 700; font-size: 30px; color: var(--brand-navy); line-height: 1; }
  .intro-block__slogan { font-family: "Ubuntu", sans-serif; font-weight: 500; font-size: 13px; color: var(--brand-blue); letter-spacing: 3px; margin-top: 4px; }
  .intro-block__lede { font-size: 12.5px; line-height: 20px; margin-top: 16px; }

  .about-copy { position: absolute; left: 118px; top: 650px; width: 724px; text-align: center; font-size: 12.5px; line-height: 20px; }
  .about-copy p + p { margin-top: 20px; }

  .site-footer { position: absolute; top: 907px; left: 0; width: 960px; height: 205px; background: var(--footer-bg); color: var(--footer-ink); text-align: center; }
  .footer-nav { display: flex; justify-content: center; gap: 27px; margin-top: 38px; }
  .footer-nav a { color: var(--footer-ink); text-decoration: none; font-size: 11.5px; }
  .social-row { display: flex; justify-content: center; gap: 7px; margin-top: 30px; }
  .social-row span { width: 18px; height: 18px; background: var(--icon-blue); border-radius: 2px; }
  .company-info { margin-top: 16px; font-size: 11px; line-height: 14px; }
</style>
</head>
<body>
  <header class="site-header">
    <div class="brand-mark"><span class="brand-mark__dot"></span><span class="brand-mark__name">OUR CLEVER DWELLING</span></div>
    <nav class="main-nav">
      <a href="#">About Us</a><a href="#">Products</a><a href="#">Shipping</a><a href="#">Support</a><a href="#">Blog</a><a href="#">Contact Us</a><a href="#">Login</a>
    </nav>
  </header>

  <section class="hero" role="img" aria-label="Blue backdrop of glowing connected network nodes and lines">
    <h1 class="hero__title">ABOUT US</h1>
  </section>

  <div class="intro-symbol"></div>
  <section class="intro-block">
    <h2 class="intro-block__name">OUR CLEVER DWELLING</h2>
    <p class="intro-block__slogan">Calm Evenings Come Naturally</p>
    <p class="intro-block__lede">The one more step which Technology moved into electronics<br>(mainly smart devices) design &amp; manufacturing business<br>based on its PCB Design &amp; Manufacturing business.</p>
  </section>

  <section class="about-copy">
    <p>Our Clever Dwelling is a professional manufacturer dedicated to the research, development and manufacturing of smart devices. We offer a range of programs for our potential partners which include wholesale program, white-label solution, EMS(Electronics Manufacturing Service) and ODM program. Basically, we can offer mature products for you to directly sell, and additionally provide you with a custom-made service to meet your requirement.</p>
    <p>Currently, our company has over 200 employees, of which over 20 engineers concentrate on smart fitness bands. Our one-stop service includes design, development, production, and after-sales service. We have built a sophisticated production line for smart fitness band business, which is equipped with advanced manufacturing technology to ensure high quality.</p>
  </section>

  <footer class="site-footer">
    <nav class="footer-nav">
      <a href="#">Home</a><a href="#">About Us</a><a href="#">Products</a><a href="#">Shipping</a><a href="#">Support</a><a href="#">Bog</a><a href="#">Contact Us</a><a href="#">Login</a>
    </nav>
    <div class="social-row"><span></span><span></span><span></span><span></span><span></span><span></span><span></span></div>
    <div class="company-info">
      <p>ABN: 47 512 903 286</p>
      <p>Office: 4/22 Larkin Street MARLOW NSW 2041</p>
      <p>Telephone: (02) 5550 1846</p>
    </div>
  </footer>
</body>
</html>
```